Form With Marla - Health and Wellness Business Card and Logo

I need a business card design with a logo for my business you can check out at www.formwithmarla.net. I want something more original, simplistic, and memorable than the basic logo I have on my site currently. I am a health and wellness coach and I offer mindset coaching and nutrition plans. I like the colour teal and dark grey/black for my theme colours. I emphasize growth, longterm change, and the whole package of "healthy mind, healthy body, healthy life". I had played around the idea of intertwining 3 M's or incorporating growth (leaves etc.) into my design. I want my expertise and experience to show through. In one glance I want people to understand with confidence I can help them accomplish anything they set their minds to. I look forward to seeing what everyone comes up with!

Industry/Entity Type

Health And Wellness

Contact Information for Business Card

Form With Marla
Marla Prentiss
BSc, Health & Wellness Coach
"Manifest your best"
www.formwithmarla.net
formwithmarla@quillpost.net
472-618-9043

Colors
33b8a4
ffffff
333333
000000

Requirements
Must have
• A memorable and unique logo for my business!
Nice to have
• Could have the phrase "Are you unhappy with your body and state of health?" or "It takes the right skills to develop habits in order to create long term change. I can help you get there."

```html
<!DOCTYPE html>
<html lang="en">
<head>
<meta charset="utf-8">
<title>Form With Marla — Business Card</title>
<link rel="stylesheet" href="https://fonts.googleapis.com/css2?family=Oswald:wght@600&family=Open+Sans:wght@300;400;600&display=swap">
<style>
  :root {
    --backdrop: #1b1b1b;
    --card: #282828;
    --teal: #2a9d8f;
    --white: #ffffff;
    --text: #d2d2d2;
    --silver: #bdbdbd;
    --rule: #8a8a8a;
  }
  * { margin: 0; padding: 0; box-sizing: border-box; }
  html, body { width: 1200px; height: 1000px; overflow: hidden; }
  body {
    background: var(--backdrop);
    font-family: "Open Sans", Arial, sans-serif;
    position: relative;
  }
  .card {
    position: absolute;
    left: 230px;
    width: 740px;
    height: 420px;
    background: var(--card);
    box-shadow: 0 10px 30px rgba(0,0,0,.45);
  }
  .card--back { top: 60px; }
  .card--front { top: 520px; }

  /* back side */
  .brand-mark {
    position: absolute;
    left: 50%; top: 50%;
    transform: translate(-50%, -50%);
    display: flex;
    align-items: center;
    gap: 18px;
  }
  .brand-mark__circle {
    width: 64px; height: 64px;
    border: 2px solid var(--silver);
    border-radius: 50%;
  }
  .brand-mark__name {
    font-weight: 400;
    font-size: 26px;
    color: var(--silver);
    letter-spacing: .5px;
    white-space: nowrap;
  }

  /* front side */
  .identity {
    position: absolute;
    right: 382px;
    top: 150px;
    text-align: right;
    white-space: nowrap;
  }
  .identity__name {
    font-family: "Oswald", "Arial Narrow", sans-serif;
    font-weight: 600;
    font-size: 38px;
    line-height: 1;
    color: var(--white);
    letter-spacing: .5px;
    text-transform: uppercase;
  }
  .identity__role {
    font-weight: 600;
    font-size: 16px;
    color: var(--teal);
    margin-top: 10px;
    letter-spacing: .5px;
  }
  .divider {
    position: absolute;
    left: 380px;
    top: 148px;
    width: 2px;
    height: 92px;
    background: var(--rule);
  }
  .contacts {
    position: absolute;
    left: 404px;
    top: 148px;
    list-style: none;
  }
  .contacts__item {
    display: flex;
    align-items: center;
    gap: 12px;
    height: 30px;
    font-weight: 300;
    font-size: 17px;
    color: var(--text);
    letter-spacing: .3px;
    white-space: nowrap;
  }
  .contacts__item svg { width: 14px; height: 14px; flex: none; fill: var(--teal); }
  .contacts__accent { color: var(--teal); font-weight: 400; }
  .tagline {
    position: absolute;
    left: 150px;
    top: 328px;
    font-weight: 300;
    font-size: 19px;
    color: var(--text);
    letter-spacing: .6px;
    white-space: nowrap;
  }
  .corner-mark {
    position: absolute;
    right: 28px;
    bottom: 26px;
    display: flex;
    align-items: center;
    gap: 8px;
  }
  .corner-mark__circle {
    width: 22px; height: 22px;
    border: 2px solid var(--teal);
    border-radius: 50%;
  }
  .corner-mark__name {
    font-weight: 400;
    font-size: 12px;
    color: var(--teal);
    white-space: nowrap;
  }
</style>
</head>
<body>

  <section class="card card--back" aria-label="Card back">
    <div class="brand-mark">
      <span class="brand-mark__circle"></span>
      <span class="brand-mark__name">Form With Marla</span>
    </div>
  </section>

  <section class="card card--front" aria-label="Card front">
    <div class="identity">
      <h1 class="identity__name">Marla Prentiss</h1>
      <p class="identity__role">BSc, Health &amp; Wellness Coach</p>
    </div>

    <span class="divider"></span>

    <ul class="contacts">
      <li class="contacts__item">
        <svg viewBox="0 0 16 16" aria-hidden="true"><path d="M3.6 1.2l2.3 2.6-1.3 1.9c.9 2 2.6 3.7 4.6 4.7l1.9-1.3 2.6 2.3-1.4 2.6C7 13.6 2.4 9 1 3z"/></svg>
        <span>472-618-9043</span>
      </li>
      <li class="contacts__item">
        <svg viewBox="0 0 16 16" aria-hidden="true"><path d="M1 3h14v10H1z"/><path d="M1.5 3.5L8 8.7l6.5-5.2" fill="none" stroke="var(--card)" stroke-width="1.4"/></svg>
        <span>formwithmarla@quillpost.net</span>
      </li>
      <li class="contacts__item">
        <svg viewBox="0 0 16 16" aria-hidden="true"><circle cx="8" cy="8" r="7"/><path d="M1 8h14M8 1c-3 3.5-3 10.5 0 14M8 1c3 3.5 3 10.5 0 14" fill="none" stroke="var(--card)" stroke-width="1.1"/></svg>
        <span>www.<span class="contacts__accent">formwithmarla</span>.net</span>
      </li>
    </ul>

    <p class="tagline">“Manifest your best”</p>

    <div class="corner-mark">
      <span class="corner-mark__circle"></span>
      <span class="corner-mark__name">Form With Marla</span>
    </div>
  </section>

</body>
</html>
```